Birchline Septic Solutions

Would like to see some single sided ones but would also like to see some double sided with one sided only being the logo. Owners name is Colin Vandro. Phone number is 555-214-0387
Services are pumping, inspections, installs, and repairs

Contact Information for Business Card

555-241-0387 Colin Vandro Maplewood, OH

```html
<!DOCTYPE html>
<html lang="en">
<head>
<meta charset="utf-8">
<title>Birchline Septic Solutions – Business Cards</title>
<link href="https://fonts.googleapis.com/css2?family=Montserrat:wght@400;500;700;800&display=swap" rel="stylesheet">
<style>
  :root {
    --ink: #0b0b0b;
    --paper: #ffffff;
    --teal: #2bb8b0;
    --backdrop: #d9d9d9;
    --muted: #2a2a2a;
  }
  * { box-sizing: border-box; margin: 0; padding: 0; }
  html, body { width: 1200px; height: 856px; overflow: hidden; }
  body {
    background: var(--backdrop);
    font-family: "Montserrat", sans-serif;
    display: flex;
    align-items: center;
    justify-content: center;
    gap: 34px;
  }
  .card {
    position: relative;
    width: 560px;
    height: 320px;
    overflow: hidden;
    box-shadow: 0 10px 28px rgba(0,0,0,0.25);
  }
  /* Front */
  .card--front { background: var(--paper); }
  .card__wave { position: absolute; inset: 0; width: 100%; height: 100%; }
  .brand {
    position: absolute;
    display: flex;
    align-items: center;
    gap: 10px;
    font-weight: 800;
    text-transform: uppercase;
    letter-spacing: 0.06em;
    line-height: 1.1;
  }
  .brand__mark { width: 14px; height: 14px; flex: none; background: var(--teal); }
  .card--front .brand {
    left: 28px; top: 88px; width: 220px;
    font-size: 19px; color: var(--ink);
  }
  .divider {
    position: absolute;
    left: 266px; top: 52px;
    width: 1.5px; height: 120px;
    background: var(--teal);
  }
  .contact {
    position: absolute;
    left: 284px; top: 46px;
    color: var(--ink);
  }
  .contact__name {
    font-weight: 800; font-size: 17px; text-transform: uppercase;
  }
  .contact__name .surname { color: var(--teal); }
  .contact__role { font-size: 12px; font-weight: 500; color: var(--muted); margin-top: 3px; }
  .contact__lines {
    display: flex; gap: 7px; margin-top: 14px;
    font-size: 12.5px; font-weight: 500; line-height: 1.35;
  }
  .contact__icon { width: 13px; height: 13px; margin-top: 18px; flex: none; }
  /* Back */
  .card--back {
    background: var(--ink);
    color: var(--paper);
    display: flex; flex-direction: column; align-items: center; justify-content: center;
    gap: 34px;
  }
  .card--back .brand {
    position: static;
    font-size: 28px; color: var(--paper);
    text-align: center;
  }
  .services {
    list-style: none;
    display: flex; flex-wrap: wrap; justify-content: center;
    gap: 4px 14px;
    width: 400px;
    font-size: 17px; font-weight: 400;
  }
  .services li { display: flex; align-items: center; gap: 6px; }
  .tick { width: 15px; height: 15px; flex: none; }
</style>
</head>
<body>

  <section class="card card--front" aria-label="Business card front">
    <svg class="card__wave" viewBox="0 0 560 320" preserveAspectRatio="none" aria-hidden="true">
      <path d="M0,305 C200,295 300,262 380,215 S500,160 560,152 L560,320 L0,320 Z" fill="var(--ink)"/>
      <path d="M180,292 C290,278 340,250 400,208 S490,170 530,164" fill="none" stroke="var(--teal)" stroke-width="4" stroke-linecap="round"/>
    </svg>

    <div class="brand">
      <span class="brand__mark"></span>
      <span>Birchline Septic Solutions</span>
    </div>

    <div class="divider"></div>

    <div class="contact">
      <p class="contact__name">Colin <span class="surname">Vandro</span></p>
      <p class="contact__role">Owners</p>
      <div class="contact__lines">
        <svg class="contact__icon" viewBox="0 0 24 24" aria-hidden="true">
          <path fill="var(--teal)" d="M6.6 10.8a15.1 15.1 0 0 0 6.6 6.6l2.2-2.2a1 1 0 0 1 1-.25 11.4 11.4 0 0 0 3.6.57 1 1 0 0 1 1 1V20a1 1 0 0 1-1 1A17 17 0 0 1 3 4a1 1 0 0 1 1-1h3.5a1 1 0 0 1 1 1c0 1.25.2 2.45.57 3.57a1 1 0 0 1-.25 1z"/>
        </svg>
        <p>555-214-0387<br>555-241-0387 Colin<br>Vandro Maplewood, OH</p>
      </div>
    </div>
  </section>

  <section class="card card--back" aria-label="Business card back">
    <div class="brand">
      <span class="brand__mark"></span>
      <span>Birchline<br>Septic Solutions</span>
    </div>
    <ul class="services">
      <li>
        <svg class="tick" viewBox="0 0 20 20" aria-hidden="true"><circle cx="10" cy="10" r="8.5" fill="none" stroke="currentColor" stroke-width="2"/><path d="M6 10.5l3 3 5-6" fill="none" stroke="currentColor" stroke-width="2" stroke-linecap="round" stroke-linejoin="round"/></svg>
        Services are pumping
      </li>
      <li>
        <svg class="tick" viewBox="0 0 20 20" aria-hidden="true"><circle cx="10" cy="10" r="8.5" fill="none" stroke="currentColor" stroke-width="2"/><path d="M6 10.5l3 3 5-6" fill="none" stroke="currentColor" stroke-width="2" stroke-linecap="round" stroke-linejoin="round"/></svg>
        inspections
      </li>
      <li>
        <svg class="tick" viewBox="0 0 20 20" aria-hidden="true"><circle cx="10" cy="10" r="8.5" fill="none" stroke="currentColor" stroke-width="2"/><path d="M6 10.5l3 3 5-6" fill="none" stroke="currentColor" stroke-width="2" stroke-linecap="round" stroke-linejoin="round"/></svg>
        installs
      </li>
      <li>
        <svg class="tick" viewBox="0 0 20 20" aria-hidden="true"><circle cx="10" cy="10" r="8.5" fill="none" stroke="currentColor" stroke-width="2"/><path d="M6 10.5l3 3 5-6" fill="none" stroke="currentColor" stroke-width="2" stroke-linecap="round" stroke-linejoin="round"/></svg>
        and repairs
      </li>
    </ul>
  </section>

</body>
</html>
```